Business cards

I would like a black background with the design I previously chose. I need 2 sets of cards. Mine will have Marlene Ridgeway, Broker/Owner, 307-481-7263 and marlene.brightharbor@quillpost.example
The second set will read, Corey Albrecht, Realtor 307-538-2409, corey.brightharbor@quillpost.example

```html
<!DOCTYPE html>
<html lang="en">
<head>
<meta charset="utf-8">
<title>Bright Harbor – Business Cards</title>
<link rel="stylesheet" href="https://fonts.googleapis.com/css2?family=Tinos:wght@400;700&display=swap">
<style>
  :root {
    --page-bg: #1a1a1b;
    --card-dark: #202022;
    --ink: #161616;
    --silver-light: #f4f4f4;
    --silver-mid: #c9c9c9;
    --silver-deep: #9a9a9a;
    --metal-dark: #1c1c1c;
  }
  html, body {
    margin: 0;
    padding: 0;
    width: 1200px;
    height: 960px;
    overflow: hidden;
    background: var(--page-bg);
  }
  .canvas {
    position: relative;
    width: 1200px;
    height: 960px;
    font-family: "Tinos", "Times New Roman", serif;
  }
  .card {
    position: absolute;
    width: 600px;
    height: 342px;
    overflow: hidden;
    box-shadow: 0 4px 14px rgba(0,0,0,0.55);
  }
  .card-front {
    left: 314px;
    top: 113px;
    background: linear-gradient(100deg, var(--silver-deep) 0%, var(--silver-light) 30%, var(--silver-mid) 55%, #e6e6e6 75%, var(--silver-deep) 100%);
  }
  .card-back {
    left: 311px;
    top: 473px;
    background: var(--card-dark);
  }
  .edge-tab {
    position: absolute;
    left: 0;
    top: 49px;
    width: 14px;
    height: 40px;
    background: var(--ink);
  }
  .feature-art {
    position: absolute;
    left: 0;
    top: 0;
    width: 600px;
    height: 342px;
  }
  .holder-name {
    position: absolute;
    left: 40px;
    top: 46px;
    margin: 0;
    font-size: 21px;
    font-weight: 700;
    color: var(--ink);
    letter-spacing: 0.2px;
  }
  .holder-title {
    position: absolute;
    left: 40px;
    top: 72px;
    margin: 0;
    font-size: 15px;
    color: var(--ink);
    letter-spacing: 0.5px;
  }
  .contact-list {
    position: absolute;
    left: 40px;
    top: 249px;
    margin: 0;
    padding: 0;
    list-style: none;
    font-size: 14px;
    line-height: 19.5px;
    color: var(--ink);
  }
  .brand {
    position: absolute;
    left: 0;
    top: 190px;
    width: 600px;
    text-align: center;
  }
  .brand-name {
    margin: 0;
    font-size: 30px;
    font-weight: 400;
    letter-spacing: 1px;
    color: var(--silver-mid);
  }
  .brand-rule {
    display: block;
    width: 250px;
    height: 1px;
    margin: 6px auto 0;
    background: var(--silver-deep);
  }
</style>
</head>
<body>
<main class="canvas">
  <section class="card card-front">
    <svg class="feature-art" viewBox="0 0 600 342" role="img" aria-label="Brushed metal circle framed by dark brush strokes with an oil pump jack silhouette">
      <defs>
        <radialGradient id="metalDisc" cx="0.62" cy="0.5" r="0.55">
          <stop offset="0" stop-color="#e2e2e2"/>
          <stop offset="0.55" stop-color="#a8a8a8"/>
          <stop offset="1" stop-color="#4a4a4a"/>
        </radialGradient>
      </defs>
      <path d="M318 0 H600 V342 H346 C290 300 262 230 268 160 C274 90 296 30 318 0 Z" fill="#1c1c1c"/>
      <path d="M345 20 C390 -5 470 -2 530 30 C585 62 600 110 600 160 V342 H360 C320 300 300 240 305 170 C310 100 325 45 345 20 Z" fill="url(#metalDisc)"/>
    </svg>
    <div class="edge-tab"></div>
    <h1 class="holder-name">MARLENE RIDGEWAY</h1>
    <p class="holder-title">BROKER/OWNER</p>
    <ul class="contact-list">
      <li>307-481-7263</li>
      <li>marlene.brightharbor@quillpost.example</li>
      <li>www.brightharbor.example</li>
    </ul>
  </section>

  <section class="card card-back">
    <div class="brand">
      <p class="brand-name">BRIGHT HARBOR</p>
      <span class="brand-rule"></span>
    </div>
  </section>
</main>
</body>
</html>
```